BUSINESS CARD DESIGN

NAME- DALE VORSKIN
PHONE NUMER - 555- 714-9082
EMAIL- OFFICE@TRV-GROUNDMAKRZ.COM
BACK OF CARD- SPEACIALIZES IN LAND CLEARING, FORESTRY MUCLHING AND EXCAVATION

Contact Information for Business Card

NAME- DALE VORSKIN PHONE NUMER - 555- 714-9082 EMAIL- OFFICE@TRV-GROUNDMAKRZ.COM BACK OF CARD- SPEACIALIZES IN LAND CLEARING , MUCLHING AND EXCAVATION

```html
<!DOCTYPE html>
<html lang="en">
<head>
<meta charset="utf-8">
<title>Terravia Groundmakrz — Business Card</title>
<link href="https://fonts.googleapis.com/css2?family=Lato:wght@400;700;900&display=swap" rel="stylesheet">
<style>
  :root {
    --stage: #2e2e2e;
    --card-dark: #141414;
    --card-dark-edge: #1e1e1e;
    --card-light: #ffffff;
    --ink: #111111;
    --ink-soft: #333333;
    --silver: #e6e6e6;
    --rule: #8a8a8a;
  }
  * { box-sizing: border-box; margin: 0; padding: 0; }
  html, body {
    width: 1200px; height: 694px; overflow: hidden;
    background: var(--stage);
    font-family: "Lato", Arial, sans-serif;
  }
  .stage {
    position: relative; width: 1200px; height: 694px;
    display: flex; align-items: center; justify-content: center; gap: 40px;
  }
  .card {
    position: relative; width: 540px; height: 309px;
    border-radius: 22px; overflow: hidden;
  }
  /* Front (dark) */
  .card--front {
    background: linear-gradient(160deg, var(--card-dark-edge), var(--card-dark));
    color: var(--silver);
  }
  .card--front .edge-line {
    position: absolute; left: 34px; top: 0; bottom: 0;
    width: 1px; background: #23233a;
  }
  .brand {
    display: flex; align-items: center; gap: 12px;
  }
  .brand__mark {
    width: 26px; height: 26px; border-radius: 50%;
  }
  .brand__name {
    font-weight: 900; letter-spacing: 2px; text-transform: uppercase;
  }
  .card--front .brand {
    position: absolute; top: 100px; left: 0; right: 0; justify-content: center;
  }
  .card--front .brand__mark { background: var(--silver); }
  .card--front .brand__name { font-size: 24px; color: var(--silver); }
  .card--front .brand-phone {
    position: absolute; top: 146px; left: 0; right: 0; text-align: center;
    font-size: 15px; font-weight: 900; letter-spacing: 6px; color: var(--silver);
  }
  .tagline {
    position: absolute; bottom: 34px; left: 0; right: 0; text-align: center;
    font-size: 16px; color: #ffffff;
  }
  /* Back (white) */
  .card--back { background: var(--card-light); color: var(--ink); }
  .card--back .brand {
    position: absolute; left: 28px; top: 120px; width: 260px; flex-direction: column; gap: 10px;
  }
  .card--back .brand__mark { background: var(--ink); width: 40px; height: 40px; }
  .card--back .brand__name { font-size: 17px; text-align: center; line-height: 1.2; color: var(--ink); }
  .card--back .brand-phone {
    font-size: 12px; font-weight: 900; letter-spacing: 5px; color: var(--ink);
  }
  .divider {
    position: absolute; left: 300px; top: 80px; height: 150px; width: 1px; background: var(--rule);
  }
  .contact {
    position: absolute; left: 322px; top: 58px; right: 16px;
  }
  .contact__name { font-size: 22px; font-weight: 900; letter-spacing: -0.3px; }
  .contact__role { font-size: 13px; color: var(--ink-soft); margin: 2px 0 14px; }
  .contact__list { list-style: none; }
  .contact__item {
    display: flex; align-items: center; gap: 9px;
    font-size: 12.5px; line-height: 1.6; color: var(--ink);
  }
  .contact__item svg { width: 13px; height: 13px; flex: none; }
  .contact__address { font-size: 12.5px; line-height: 1.45; margin-top: 12px; color: var(--ink); }
</style>
</head>
<body>
<main class="stage">
  <section class="card card--front" aria-label="Card front">
    <span class="edge-line"></span>
    <div class="brand">
      <span class="brand__mark"></span>
      <span class="brand__name">Terravia Groundmakrz LLC</span>
    </div>
    <div class="brand-phone">555-714-9082</div>
    <p class="tagline">Speacializes In Land Clearing , Muclhing And Excavation</p>
  </section>

  <section class="card card--back" aria-label="Card back">
    <div class="brand">
      <span class="brand__mark"></span>
      <span class="brand__name">Terravia Groundmakrz LLC</span>
      <span class="brand-phone">555-714-9082</span>
    </div>
    <span class="divider"></span>
    <div class="contact">
      <h1 class="contact__name">DALE VORSKIN</h1>
      <p class="contact__role">Owner</p>
      <ul class="contact__list">
        <li class="contact__item">
          <svg viewBox="0 0 16 16"><circle cx="8" cy="8" r="7.5" fill="#111"/><path d="M5 4.5l1.6-.3 1 2.2-1 .8a5 5 0 0 0 2.2 2.2l.8-1 2.2 1-.3 1.6c-3.5.3-6.8-3-6.5-6.5z" fill="#fff"/></svg>
          555- 714-9082
        </li>
        <li class="contact__item">
          <svg viewBox="0 0 16 16"><rect x="1" y="3" width="14" height="10" fill="#111"/><path d="M1 3l7 6 7-6" fill="none" stroke="#fff" stroke-width="1.2"/></svg>
          Office@trv-groundmakrz.com
        </li>
        <li class="contact__item">
          <svg viewBox="0 0 16 16"><circle cx="8" cy="8" r="7.5" fill="#111"/><path d="M1 8h14M8 .5c-3 3.5-3 11.5 0 15M8 .5c3 3.5 3 11.5 0 15" fill="none" stroke="#fff" stroke-width="1"/></svg>
          www.websitename.com
        </li>
      </ul>
      <p class="contact__address">421, Address line goes here<br>45452, Country name</p>
    </div>
  </section>
</main>
</body>
</html>
```